Quimbly Needs a 1 Page Redesign with UI/UX Elements

Quimbly is a GIF creation and sharing site. We are upgrading one of our main responsive website pages. [Please see: http://quimblyzone.net/R-4TzLa for an example]

Need design versions for Desktop, tablet & mobile.

Also need frontend development to implement page. Currently on Foundation framework.

There are many functions/nav elements that need to be on this page in an uncluttered and clear manner. Not all of functions need to be shown at all times. Need a designer with UI/UX background to incorporate these and make it easy to navigate for the user.

The designer needs to be familiar with the site to understand each function. Color scheme will remain the same as current site.

If there are Dropdowns/collapsed or hidden features - need to know how they look when opened.

Target Market(s)

Quimbly has a varied demographic but focuses on under 25.

Coding

Coded - Design and coding required

Number of Pages Required

1 page

Font styles to use
Sans Serif

Requirements
Must have
• The top and bottom nav bars must stay the same. We are not redesigning the whole site yet, just that page.
• This page is developed with sharing in mind. Our top 3 actions are highlighted below. Be creative & think about user experience as our #1 priority
• Desktop
•  SOCIAL SHARE BUTTONS Zentrova/Plinkit/Voxmora/Brolendar
•  Download Button
•  Create a GIF Button
• OTHER FEATURES THAT MUST BE INCLUDED
• Share This With Friends pop up
• Title of GIF
• Added XX days ago by XXXX in XXX
• Source
• Thumbs up votes showing numerically (no down vote thumb)
• Total Views
• Embed Links: direct, website, message board, markdown
• NSFW Flag
• MP4 to GIF toggle
• Next arrows to scroll through GIFs
• Scroll thumbnail bar for like GIFs at the bottom of the page
• NEW FEATURES TO IMPLEMENT
• Favorite (bookmark Option)
• LOGGED IN USERS:
• Logged in users also have Private Button & Delete Button
• MOBILE
• We would like to keep the mobile page as minimalist as possible.
• Download button
• Create a GIF button
• Sharing button: Drovanel, Zentrova, Plinkit, Voxmora,
• Share Via SMS
• (Please incorporate the share buttons in a creative & clean way)
• Three dots that would open up to reveal tags
• Thumbnail scroll at bottom for GIFs in the same category
Nice to have
• Be creative with how the page features are laid out. We want it to be easy for users to navigate & clear what actions are there.
Should not have
• Basically anything that is on the page now. The buttons don't look like buttons & there is no drive to any actions (like sharing). Please see attached file for what NOT to do.

```html
<!DOCTYPE html>
<html lang="en">
<head>
<meta charset="utf-8">
<title>Quimbly – GIF page</title>
<link rel="stylesheet" href="https://fonts.googleapis.com/css2?family=Open+Sans:wght@400;600;700;800&display=swap">
<style>
:root{
  --yellow:#f4b71a;
  --yellow-dark:#d99a0b;
  --ink:#222;
  --nav:#2a2a2a;
  --dark:#2f2f2f;
  --grey:#8a8a8a;
  --light:#f4f4f4;
  --white:#fff;
  --link:#2ab3e6;
}
*{box-sizing:border-box;margin:0;padding:0}
html,body{width:828px;height:1200px;overflow:hidden}
body{font-family:"Open Sans",Arial,sans-serif;color:var(--ink);background:var(--white);position:relative}

/* top nav */
.topnav{height:56px;background:var(--nav);display:flex;align-items:center;padding:0 28px}
.brand{display:flex;align-items:center;gap:7px;color:var(--white);font-weight:800;font-size:19px}
.brand-mark{width:20px;height:20px;background:var(--yellow);border-radius:3px}
.menu{display:flex;gap:15px;margin-left:58px;font-size:9.5px;font-weight:600;color:var(--white)}
.auth{margin-left:auto;display:flex;gap:8px}
.pill{font-size:9px;font-weight:700;padding:5px 14px;border-radius:12px;color:var(--white)}
.pill.login{background:var(--yellow)}
.pill.signup{background:#666}

/* hero */
.hero{position:absolute;top:56px;left:0;width:828px;height:444px;background:linear-gradient(180deg,#f7c632,var(--yellow) 60%,var(--yellow-dark))}
.viewer{position:absolute;left:124px;top:24px;width:576px;height:392px;background:var(--white);box-shadow:0 6px 18px rgba(0,0,0,.25)}
.viewer-photo{position:absolute;left:0;top:0;width:576px;height:344px;background:linear-gradient(135deg,#c9c6c0,#e8e4dc 45%,#8f9aa3)}
.viewer-head{position:absolute;left:0;top:0;width:100%;height:58px;background:rgba(0,0,0,.55);padding:10px 16px;color:var(--white)}
.gif-title{color:var(--yellow);font-weight:700;font-size:15px}
.gif-meta{font-size:9.5px}
.head-actions{position:absolute;right:16px;top:18px;display:flex;gap:8px}
.btn{font-size:9px;font-weight:700;padding:5px 14px;border-radius:12px}
.btn.download{background:var(--yellow);color:var(--white)}
.btn.create{background:var(--white);color:var(--ink);border:1px solid #ccc}
.arrow{position:absolute;top:160px;width:20px;height:30px}
.arrow.prev{left:10px}.arrow.next{right:10px}
.viewer-bar{position:absolute;left:0;bottom:0;width:100%;height:48px;display:flex;align-items:center;padding:0 16px;gap:14px}
.toggle{margin-left:auto;display:flex;border-radius:12px;overflow:hidden;font-size:9px;font-weight:700}
.toggle span{padding:5px 12px;background:#ddd;color:#666}
.toggle span.on{background:var(--yellow);color:var(--white)}
.close{width:24px;height:24px;border-radius:50%;background:var(--ink)}
.share-rail{position:absolute;left:100px;top:72px;width:24px;height:150px;background:#1e1e1e;display:flex;flex-direction:column;justify-content:space-around;align-items:center}
.share-rail span{writing-mode:vertical-rl;transform:rotate(180deg);color:var(--white);font-size:7px;font-weight:700}
.share-tab{position:absolute;left:700px;top:72px;width:24px;height:200px;background:#1e1e1e;color:var(--white);font-size:9px;font-weight:700;writing-mode:vertical-rl;display:flex;align-items:center;justify-content:center}

/* funny gifs */
.funny{position:absolute;top:500px;left:0;width:828px;height:330px;background:var(--light)}
.section-title{text-align:center;font-size:15px;font-weight:700;padding-top:40px}
.grid{display:flex;gap:14px;justify-content:center;margin-top:22px}
.card{width:140px;background:var(--white);padding:0 0 10px;box-shadow:0 1px 3px rgba(0,0,0,.12)}
.card-photo{height:92px;background:linear-gradient(135deg,#7fb7dc,#e7c49a)}
.card-body{padding:7px 8px 0}
.card-title{color:var(--yellow);font-size:10px;font-weight:700}
.card-meta{font-size:7px;color:#555}
.card-share{display:flex;align-items:center;gap:5px;font-size:7px;font-weight:700;margin:8px 0}
.dot{width:8px;height:8px;border-radius:50%;background:#999}
.card-actions{display:flex;gap:5px}
.card-actions .btn{font-size:7px;padding:4px 8px}

/* feed */
.feed{position:absolute;top:830px;left:0;width:828px;height:262px;background:var(--dark)}
.feed-head{display:flex;align-items:center;padding:26px 128px 0;color:var(--white);font-size:12px;font-weight:700;gap:7px}
.feed-head .mark{width:10px;height:10px;border-radius:50%;background:var(--link)}
.feed-head .upload{margin-left:auto;background:var(--white);color:var(--ink);font-size:8px;padding:5px 12px;border-radius:12px}
.feed-row{display:flex;gap:16px;justify-content:center;margin-top:16px}
.post{width:180px;color:var(--white)}
.post-photo{height:108px;background:linear-gradient(135deg,#e49b4a,#b1566b)}
.post-foot{display:flex;justify-content:space-between;align-items:center;margin-top:8px}
.post-name{font-size:9px;font-weight:700}
.post-link{font-size:8px;color:var(--link)}
.star{width:16px;height:16px;background:var(--yellow);border-radius:2px}
.pager{display:flex;gap:6px;justify-content:center;margin-top:18px}
.pager i{width:6px;height:6px;border-radius:50%;background:#777}
.pager i.on{background:var(--yellow)}

/* footer */
.footer{position:absolute;top:1092px;left:0;width:828px;text-align:center}
.footer-social{display:flex;gap:4px;justify-content:center;margin-top:14px}
.footer-social span{width:18px;height:18px;border-radius:50%;background:#1d5aa0}
.footer-links{font-size:8px;color:#555;margin-top:10px;word-spacing:2px}
.copyright{font-size:7.5px;color:#888;margin-top:6px}
</style>
</head>
<body>

<header class="topnav">
  <div class="brand"><span class="brand-mark"></span>Quimbly</div>
  <nav class="menu">
    <span>The Gallery</span><span>Pictures to GIF</span><span>Clipstream to GIF</span><span>Upload a GIF</span><span>Video to GIF</span><span>Webcam to GIF</span>
  </nav>
  <div class="auth"><span class="pill login">LOGIN</span><span class="pill signup">SIGN UP</span></div>
</header>

<section class="hero">
  <div class="share-rail">
    <span>Zentrova</span><span>Plinkit</span><span>Brolendar</span><span>Drovanel</span>
  </div>
  <div class="viewer">
    <div class="viewer-photo" role="img" aria-label="Animated GIF of friends working together at a laptop"></div>
    <div class="viewer-head">
      <div class="gif-title">Whiteboys</div>
      <div class="gif-meta">Added last week anonymously in Funny gifs</div>
      <div class="head-actions"><span class="btn download">Download</span><span class="btn create">Create a GIF</span></div>
    </div>
    <svg class="arrow prev" viewBox="0 0 20 30"><path d="M14 4 4 15l10 11" fill="none" stroke="#fff" stroke-width="3"/></svg>
    <svg class="arrow next" viewBox="0 0 20 30"><path d="M6 4l10 11L6 26" fill="none" stroke="#fff" stroke-width="3"/></svg>
    <div class="viewer-bar">
      <svg width="14" height="13" viewBox="0 0 14 13"><path d="M7 12 1.5 6.5A3.2 3.2 0 0 1 7 2.5a3.2 3.2 0 0 1 5.5 4z" fill="#999"/></svg>
      <svg width="14" height="14" viewBox="0 0 14 14"><path d="M5 9l4-4M6 3.5l1.5-1.5a2.5 2.5 0 0 1 3.5 3.5L9.5 7M8 10.5 6.5 12A2.5 2.5 0 0 1 3 8.5L4.5 7" fill="none" stroke="#999" stroke-width="1.5"/></svg>
      <svg width="16" height="12" viewBox="0 0 16 12"><path d="M1 6s3-5 7-5 7 5 7 5-3 5-7 5-7-5-7-5z" fill="none" stroke="#999" stroke-width="1.4"/><circle cx="8" cy="6" r="2" fill="#999"/></svg>
      <div class="toggle"><span class="on">GIF</span><span>MP4</span></div>
      <span class="close"></span>
    </div>
  </div>
  <div class="share-tab">Share This With Friends</div>
</section>

<section class="funny">
  <h2 class="section-title">CHECK OUT THESE FUNNY GIFS</h2>
  <div class="grid">
    <article class="card"><div class="card-photo" role="img" aria-label="GIF thumbnail of friends at a laptop"></div><div class="card-body"><div class="card-title">Whiteboys</div><div class="card-meta">Added last week anonymously in Funny gifs</div><div class="card-share">Social Share <i class="dot"></i><i class="dot"></i><i class="dot"></i><i class="dot"></i></div><div class="card-actions"><span class="btn download">Download</span><span class="btn create">Create a GIF</span></div></div></article>
    <article class="card"><div class="card-photo" role="img" aria-label="GIF thumbnail of friends on a beach"></div><div class="card-body"><div class="card-title">Whiteboys</div><div class="card-meta">Added last week anonymously in Funny gifs</div><div class="card-share">Social Share <i class="dot"></i><i class="dot"></i><i class="dot"></i><i class="dot"></i></div><div class="card-actions"><span class="btn download">Download</span><span class="btn create">Create a GIF</span></div></div></article>
    <article class="card"><div class="card-photo" role="img" aria-label="GIF thumbnail of a group taking a selfie"></div><div class="card-body"><div class="card-title">Whiteboys</div><div class="card-meta">Added last week anonymously in Funny gifs</div><div class="card-share">Social Share <i class="dot"></i><i class="dot"></i><i class="dot"></i><i class="dot"></i></div><div class="card-actions"><span class="btn download">Download</span><span class="btn create">Create a GIF</span></div></div></article>
    <article class="card"><div class="card-photo" role="img" aria-label="GIF thumbnail of friends laughing outdoors"></div><div class="card-body"><div class="card-title">Whiteboys</div><div class="card-meta">Added last week anonymously in Funny gifs</div><div class="card-share">Social Share <i class="dot"></i><i class="dot"></i><i class="dot"></i><i class="dot"></i></div><div class="card-actions"><span class="btn download">Download</span><span class="btn create">Create a GIF</span></div></div></article>
  </div>
</section>

<section class="feed">
  <div class="feed-head"><span class="mark"></span>PLINKIT<span class="upload">Upload GIF</span></div>
  <div class="feed-row">
    <article class="post"><div class="post-photo" role="img" aria-label="Shared GIF of friends at a party"></div><div class="post-foot"><div><div class="post-name">Quimbly Animated GIFs</div><div class="post-link">qmb.ly/4kT2vX</div></div><span class="star"></span></div></article>
    <article class="post"><div class="post-photo" role="img" aria-label="Shared GIF of friends hugging"></div><div class="post-foot"><div><div class="post-name">Quimbly Animated GIFs</div><div class="post-link">qmb.ly/8rN5qP</div></div><span class="star"></span></div></article>
    <article class="post"><div class="post-photo" role="img" aria-label="Shared GIF of a crowd at a concert"></div><div class="post-foot"><div><div class="post-name">Quimbly Animated GIFs</div><div class="post-link">qmb.ly/2zH7mL</div></div><span class="star"></span></div></article>
  </div>
  <div class="pager"><i class="on"></i><i></i><i></i><i></i></div>
</section>

<footer class="footer">
  <div class="footer-social"><span></span><span></span><span></span></div>
  <div class="footer-links">Upload a GIF | Video to GIF | Webcam to GIF | Clipstream to GIF | Privacy Policy | Contact Us | Request Deletion</div>
  <div class="copyright">© 2015 Quimbly, All Rights Reserved.</div>
</footer>

</body>
</html>
```